Brindle Yard Care. The best in the biz

I run a lawn care service that offers full service mowing. 100% satisfaction guarantee. Fast, Friendly, quality service "I am your lawns best friend" I cut residential lawns. I offer a mow package that includes trimming, edging and clean up. Prices very from 20 dollars to 75. I want my logo to stand out. Free estimates

Target Market(s)

Home owners

Industry/Entity Type

Landscaping

Contact Information for Business Card

555-812-4473 tomvale48@quillmail.net Derek. Brindle Yard care

Colors
f37122
9bcb3c
cadf82

Requirements
Must have
• Company name.
• Phone number
• Email
• My services
• images
Nice to have
• A sun that is growing grass.
Should not have
• Incorrect information

```html
<!DOCTYPE html>
<html lang="en">
<head>
<meta charset="utf-8">
<title>Brindle Yard Care – Business Card</title>
<link href="https://fonts.googleapis.com/css2?family=Roboto:wght@400&family=Source+Sans+3:wght@400;600&display=swap" rel="stylesheet">
<style>
  :root {
    --lawn-green: #9bcb3c;
    --sun-orange: #f37122;
    --slate: #5b5b5b;
    --ink: #444444;
    --paper: #ffffff;
    --backdrop-top: #222222;
    --backdrop-bottom: #050505;
  }
  * { margin: 0; padding: 0; box-sizing: border-box; }
  html, body { width: 1200px; height: 900px; overflow: hidden; }
  body {
    position: relative;
    background: linear-gradient(180deg, var(--backdrop-top) 0%, var(--backdrop-bottom) 100%);
    font-family: "Source Sans 3", "Helvetica Neue", Arial, sans-serif;
  }
  .card {
    position: absolute;
    top: 170px;
    width: 347px;
    height: 561px;
  }
  .card--front { left: 259px; background: var(--paper); }
  .card--back  { left: 631px; background: var(--lawn-green); }

  .tab {
    position: absolute;
    left: 101px;
    width: 144px;
    background: var(--lawn-green);
  }
  .tab--top { top: 0; height: 30px; }
  .tab--bottom { bottom: 0; height: 28px; }

  .front-mark {
    position: absolute;
    left: 124px;
    top: 137px;
    width: 88px;
    height: 88px;
    border-radius: 50%;
    background: var(--lawn-green);
  }
  .company-name {
    position: absolute;
    top: 230px;
    width: 100%;
    text-align: center;
    font-family: "Roboto", Arial, sans-serif;
    font-weight: 400;
    font-size: 33px;
    color: var(--lawn-green);
  }
  .contact-name {
    position: absolute;
    top: 313px;
    width: 100%;
    text-align: center;
    font-weight: 600;
    font-size: 19px;
    color: var(--lawn-green);
  }
  .contact-list {
    position: absolute;
    top: 362px;
    width: 100%;
    list-style: none;
    text-align: center;
    font-size: 15.5px;
    line-height: 20px;
    color: var(--ink);
  }
  .contact-list li { display: flex; justify-content: center; align-items: center; gap: 7px; }
  .contact-list svg { fill: var(--lawn-green); }

  .back-mark {
    position: absolute;
    left: 55px;
    top: 62px;
    width: 236px;
    height: 236px;
    border-radius: 50%;
    background: var(--slate);
    display: flex;
    align-items: center;
    justify-content: center;
  }
  .back-mark span {
    font-weight: 600;
    font-size: 24px;
    color: var(--paper);
  }
  .taglines {
    position: absolute;
    top: 342px;
    width: 100%;
    list-style: none;
    text-align: center;
    font-weight: 600;
    font-size: 21px;
    color: var(--paper);
  }
  .taglines li { height: 50px; }
  .taglines li:nth-child(2) { height: 52px; }
</style>
</head>
<body>
  <section class="card card--front">
    <div class="tab tab--top"></div>
    <div class="front-mark" aria-hidden="true"></div>
    <h1 class="company-name">Brindle Yard Care</h1>
    <p class="contact-name">Derek</p>
    <ul class="contact-list">
      <li>
        <svg width="12" height="12" viewBox="0 0 24 24" aria-hidden="true"><path d="M6.6 10.8a15.1 15.1 0 0 0 6.6 6.6l2.2-2.2a1 1 0 0 1 1-.25 11.4 11.4 0 0 0 3.6.57 1 1 0 0 1 1 1V20a1 1 0 0 1-1 1A17 17 0 0 1 3 4a1 1 0 0 1 1-1h3.5a1 1 0 0 1 1 1c0 1.25.2 2.45.57 3.57a1 1 0 0 1-.25 1z"/></svg>
        555-812-4473
      </li>
      <li>
        <svg width="11" height="9" viewBox="0 0 22 16" aria-hidden="true"><path d="M0 0h22v16H0z M2 2v1l9 6 9-6V2z" fill-rule="evenodd"/></svg>
        tomvale48@quillmail.net
      </li>
    </ul>
    <div class="tab tab--bottom"></div>
  </section>

  <section class="card card--back">
    <div class="back-mark"><span>Brindle Yard Care</span></div>
    <ul class="taglines">
      <li>100% satisfaction guarantee.</li>
      <li>Fast, Friendly, Quality Service</li>
      <li>I am your lawns best friend</li>
    </ul>
  </section>
</body>
</html>
```